Recruiting ad for Caregivers and Nurses

We need a few amazing, fun, catchy, creative recruiting ads for Caregivers and Nurses to care for homecare patients on the island of Oahu, in Hawaii. We are an in home care company called Palmer Homecare. Our care services are provided 24/7, so we need staff that can work days, nights, weekdays, weekends. We need catchy fun ads to entice caregivers and nurses to call our office to inquire about jobs available. Our patients age range is from babies to seniors. We need caregivers and nurses for basic patient care (bathing, dressing, ambulating, preparing meals, medication reminders, light housekeeping) and complex patients (oxygen, tube feeding, injections, vents, wound care). Here are some bullets to consider including:
*Full-time and Part-time Positions Available (days, nights, weekdays, weekends)
*Sign-On Bonus Programs Offered up to $500
*Refer a Friend Bonus Program
*Holiday Pay
*2 Health Plans to Choose from
*Island-Wide Locations
*All PPE Provided (masks, gloves, etc)
*401K Program
*Tuition Benefits

```html
<!DOCTYPE html>
<html lang="en">
<head>
<meta charset="utf-8">
<title>Palmer Homecare – Caregivers Recruiting Flyer</title>
<link rel="stylesheet" href="https://fonts.googleapis.com/css2?family=Marcellus&family=Parisienne&family=Arimo:wght@400;700&display=swap">
<style>
  :root {
    --canvas-bg: #eceef1;
    --paper: #ffffff;
    --teal-dark: #1f5f5c;
    --teal: #6cc2b7;
    --mint: #cdeae6;
    --mint-light: #e6f5f2;
    --peach: #f0957a;
    --slate: #3e6572;
    --ink-white: #ffffff;
    --serif: "Marcellus", Georgia, serif;
    --script: "Parisienne", cursive;
    --sans: "Arimo", Arial, sans-serif;
  }
  * { box-sizing: border-box; margin: 0; padding: 0; }
  html, body { width: 1200px; height: 1200px; overflow: hidden; }
  body { background: var(--canvas-bg); position: relative; }

  .flyer {
    position: absolute; left: 175px; top: 50px;
    width: 850px; height: 1100px;
    background: var(--paper);
    overflow: hidden;
  }
  .flyer svg { position: absolute; left: 0; top: 0; width: 850px; height: 1100px; }

  .headline {
    position: absolute; right: 24px; top: 18px;
    text-align: right; color: var(--teal-dark);
    font-family: var(--serif); font-size: 62px; line-height: 1.05;
  }
  .headline .script { font-family: var(--script); color: var(--peach); font-size: 58px; margin-right: 8px; }

  .brand {
    position: absolute; left: 499px; top: 408px; width: 336px; height: 336px;
    display: flex; flex-direction: column; align-items: center; justify-content: center;
    color: var(--teal-dark); font-family: var(--serif); text-align: center;
  }
  .brand-dot { width: 48px; height: 48px; border-radius: 50%; background: var(--peach); margin-bottom: 14px; }
  .brand-name { font-size: 64px; line-height: 1; }
  .brand-sub { font-size: 22px; letter-spacing: 8px; margin-top: 6px; }

  .recruit { position: absolute; left: 26px; top: 640px; font-family: var(--sans); font-weight: 700; }
  .recruit-kicker { color: var(--peach); font-size: 30px; letter-spacing: 0.5px; }
  .recruit-title { color: var(--teal-dark); font-size: 49px; line-height: 1.05; letter-spacing: 1px; }
  .recruit-rule { width: 332px; height: 5px; background: var(--teal); margin-top: 6px; }

  .perks {
    position: absolute; left: 140px; width: 620px; top: 758px;
    list-style: none; text-align: center;
    font-family: var(--sans); font-weight: 700; font-size: 23px; color: var(--teal-dark);
    line-height: 31.5px;
  }
  .perks li::before {
    content: ""; display: inline-block; width: 12px; height: 12px; border-radius: 50%;
    background: var(--peach); margin-right: 10px; vertical-align: 2px;
  }
  .perks .light { font-weight: 400; }

  .care-scope {
    position: absolute; left: 22px; top: 962px; width: 380px;
    font-family: var(--sans); font-size: 20px; line-height: 29px; color: var(--ink-white);
  }
  .care-scope h3 { color: var(--peach); font-size: 20px; font-weight: 700; }

  .contact {
    position: absolute; right: 24px; top: 968px; text-align: right;
  }
  .contact-label { font-family: var(--serif); font-size: 40px; color: var(--teal-dark); }
  .contact-phone {
    display: flex; align-items: center; justify-content: flex-end; gap: 10px;
    font-family: var(--sans); font-size: 40px; color: var(--ink-white); margin-top: 2px;
  }
  .contact-phone svg { position: static; width: 44px; height: 44px; }
</style>
</head>
<body>
<div class="flyer">
  <svg class="flyer-backdrop" viewBox="0 0 850 1100" aria-hidden="true">
    <defs>
      <linearGradient id="mintWash" x1="0" y1="0" x2="1" y2="1">
        <stop offset="0" stop-color="#eef8f6"/>
        <stop offset="1" stop-color="#bfe3de"/>
      </linearGradient>
    </defs>
    <path d="M0,0 H850 V340 C650,250 350,160 0,160 Z" fill="url(#mintWash)"/>
    <path d="M0,0 H110 C320,40 600,170 850,268 V312 C620,215 320,95 0,60 Z" fill="var(--peach)"/>
  </svg>

  <svg class="photo-area" viewBox="0 0 850 1100" role="img" aria-label="Photo of a smiling caregiver in blue scrubs sitting on a sofa with a senior woman in a bright living room">
    <defs>
      <linearGradient id="photoTones" x1="0" y1="0" x2="1" y2="1">
        <stop offset="0" stop-color="#e8d88a"/>
        <stop offset="0.45" stop-color="#c9a76a"/>
        <stop offset="0.7" stop-color="#5fa6c4"/>
        <stop offset="1" stop-color="#a9793f"/>
      </linearGradient>
    </defs>
    <path d="M0,160 C300,150 600,235 850,335 V745 C720,700 620,618 430,612 C250,606 110,560 0,490 Z" fill="url(#photoTones)"/>
  </svg>

  <svg class="flyer-shapes" viewBox="0 0 850 1100" aria-hidden="true">
    <path d="M0,496 C110,566 250,614 430,620 C620,626 720,706 850,754" fill="none" stroke="var(--teal)" stroke-width="10"/>
    <path d="M0,940 C220,925 400,918 620,962 L440,1100 H0 Z" fill="var(--slate)"/>
    <path d="M420,1100 C520,985 650,895 850,850 V935 C650,965 560,1015 490,1100 Z" fill="var(--mint)"/>
    <path d="M490,1100 C560,1015 650,965 850,935 V1100 Z" fill="var(--peach)"/>
    <circle cx="667" cy="576" r="178" fill="#eef1f1"/>
    <circle cx="667" cy="576" r="168" fill="var(--paper)" stroke="var(--peach)" stroke-width="3"/>
  </svg>

  <h1 class="headline">Retirement<br><span class="script">with</span>Purpose</h1>

  <div class="brand">
    <span class="brand-dot"></span>
    <span class="brand-name">Palmer</span>
    <span class="brand-sub">HOMECARE</span>
  </div>

  <div class="recruit">
    <p class="recruit-kicker">SEEKING COMPASSIONATE</p>
    <h2 class="recruit-title">CAREGIVERS</h2>
    <div class="recruit-rule"></div>
  </div>

  <ul class="perks">
    <li>FLEXIBLE SCHEDULE</li>
    <li>BONUS PROGRAM UP TO $500</li>
    <li>MEDICAL / DENTAL / VISION</li>
    <li>All PPE Provided <span class="light">(Masks, gloves, etc)</span></li>
    <li>ISLAND-WIDE LOCATIONS</li>
  </ul>

  <div class="care-scope">
    <h3>BASIC PATIENT CARE</h3>
    <p>(Companionship, bathing, dressing, preparing meals, medication reminders, light housekeeping)</p>
  </div>

  <div class="contact">
    <p class="contact-label">Call Us</p>
    <p class="contact-phone">
      <svg viewBox="0 0 44 44" aria-hidden="true">
        <circle cx="22" cy="22" r="21" fill="var(--slate)"/>
        <path d="M15.5,12 l4,0 l1.6,5 l-2.6,2 c1.3,2.8 3.4,4.9 6.2,6.2 l2,-2.6 l5,1.6 l0,4 c0,1.2 -1,2 -2.2,2 C20.3,30 14,23.7 13.8,14.2 C13.8,13 14.4,12 15.5,12 Z" fill="var(--ink-white)"/>
      </svg>
      808-555-0142
    </p>
  </div>
</div>
</body>
</html>
```